Business Cards - Brightpath Horizon

need to design unique business card for my mortgage business. I need to design credit card style business card for my business or any unique idea that you might have

Target Market(s)

Home Loan customers

Industry/Entity Type

Mortgage Brokerage

Contact Information for Business Card

please design credit card style or very unique style business card

Colors

Designer to choose colors to be used in the design.

Requirements
Must have
• Name
• position
• Phone number
• fax number
• email address
• website address
• social media address
• All above fields will be provided once design in finalised

```html
<!DOCTYPE html>
<html lang="en">
<head>
<meta charset="utf-8">
<title>Brightpath Horizon – Business Card</title>
<link rel="stylesheet" href="https://fonts.googleapis.com/css2?family=Work+Sans:wght@400;500;600&display=swap">
<style>
  :root {
    --bg: #1c1c1c;
    --orange: #f28a22;
    --navy: #263f9a;
    --sky: #2aa3e0;
    --ink: #3a3a3a;
    --muted: #5c5c5c;
    --white: #ffffff;
  }
  * { margin: 0; padding: 0; box-sizing: border-box; }
  html, body { width: 1200px; height: 963px; overflow: hidden; }
  body {
    background: var(--bg);
    font-family: "Work Sans", sans-serif;
    position: relative;
  }
  .card {
    position: absolute;
    left: 250px;
    width: 700px;
    height: 400px;
    border-radius: 22px;
    overflow: hidden;
  }
  .card--front { top: 60px; background: var(--white); }
  .card--back  { top: 503px; background: var(--orange); }

  /* Front */
  .front-brand {
    position: absolute;
    left: 40px; top: 0; width: 300px; height: 100%;
    display: flex; align-items: center; justify-content: center;
  }
  .brand-name {
    font-family: "Work Sans", sans-serif;
    font-weight: 600;
    font-size: 34px;
    line-height: 1.05;
    text-align: center;
    color: var(--navy);
    letter-spacing: 1px;
    text-transform: uppercase;
  }
  .divider {
    position: absolute;
    left: 360px; top: 70px;
    width: 2px; height: 260px;
    background: var(--sky);
  }
  .contact {
    position: absolute;
    left: 395px; top: 78px; right: 30px;
    color: var(--ink);
  }
  .contact-name {
    font-size: 28px; font-weight: 500;
    letter-spacing: 3px; text-transform: uppercase;
    color: var(--sky);
  }
  .contact-role { font-size: 16px; font-weight: 500; margin-top: 2px; color: var(--ink); }
  .contact-address { margin-top: 22px; font-size: 15px; line-height: 1.4; color: var(--muted); }
  .contact-list { list-style: none; margin-top: 20px; font-size: 15px; line-height: 1.5; color: var(--muted); }
  .contact-list li { display: flex; align-items: center; gap: 9px; }
  .contact-list svg { width: 12px; height: 12px; flex: none; }

  /* Back */
  .back-brand {
    position: absolute; inset: 0;
    display: flex; align-items: center; justify-content: center;
    padding-bottom: 30px;
  }
  .back-brand .brand-name { color: var(--white); font-size: 46px; }
  .back-web {
    position: absolute; left: 0; right: 0; bottom: 42px;
    text-align: center; color: var(--white);
    font-size: 17px; letter-spacing: 2px;
  }
</style>
</head>
<body>
  <section class="card card--front">
    <div class="front-brand">
      <div class="brand-name">Brightpath<br>Horizon</div>
    </div>
    <div class="divider"></div>
    <div class="contact">
      <div class="contact-name">Daniel Reyes</div>
      <div class="contact-role">Founder</div>
      <div class="contact-address">482 Linden Ave.<br>Coral Bay, FL 33010</div>
      <ul class="contact-list">
        <li>
          <svg viewBox="0 0 12 12" aria-hidden="true"><path d="M2.5 1 L4.5 1 L5 3.5 L3.8 4.4 Q5 7 7.6 8.2 L8.5 7 L11 7.5 L11 9.5 Q10.5 11 9 11 Q1 10 1 2.5 Q1 1 2.5 1 Z" fill="var(--sky)"/></svg>
          555-014-2290
        </li>
        <li>
          <svg viewBox="0 0 12 12" aria-hidden="true"><rect x="1" y="2.5" width="10" height="7" rx="1" fill="none" stroke="var(--sky)" stroke-width="1.3"/><path d="M1.5 3 L6 6.5 L10.5 3" fill="none" stroke="var(--sky)" stroke-width="1.3"/></svg>
          hello@brightpathhorizon.com
        </li>
        <li>
          <svg viewBox="0 0 12 12" aria-hidden="true"><circle cx="6" cy="6" r="5" fill="none" stroke="var(--sky)" stroke-width="1.2"/><ellipse cx="6" cy="6" rx="2.2" ry="5" fill="none" stroke="var(--sky)" stroke-width="1"/><line x1="1" y1="6" x2="11" y2="6" stroke="var(--sky)" stroke-width="1"/></svg>
          www.brightpathhorizon.com
        </li>
      </ul>
    </div>
  </section>

  <section class="card card--back">
    <div class="back-brand">
      <div class="brand-name">Brightpath<br>Horizon</div>
    </div>
    <div class="back-web">www.yourwebsite.com</div>
  </section>
</body>
</html>
```